design a construction company business card

Design business card around our logo. Card must have all the typical info: name, title, address, phone, email, business name, etc. Somewhere on the card I would like to see our motto "Built on integrity... Inspired by commitment." Consider adding a splash of bright orange to the card to complement the blues and silvers/grays in the logo. We are open to metallic inks, textures, etc. We would like to see options on both light and dark backgrounds. The font in the logo is Euro Technic Extended Regular.

```html
<!DOCTYPE html>
<html lang="en">
<head>
<meta charset="utf-8">
<title>Harlow Building – Business Card</title>
<link rel="stylesheet" href="https://fonts.googleapis.com/css2?family=Open+Sans:wght@400;600&display=swap">
<style>
  :root {
    --page: #ffffff;
    --card-light: #e6e6e7;
    --card-dark: #808184;
    --brand-blue: #1f6fb8;
    --name-blue: #1f7bc1;
    --text-grey: #58595b;
    --rule-grey: #9a9b9e;
    --accent-orange: #f7941d;
    --skyline-blue: #a6bfdc;
    --skyline-lilac: #b3b3d6;
    --white: #ffffff;
  }
  * { box-sizing: border-box; margin: 0; padding: 0; }
  html, body {
    width: 800px; height: 1200px; overflow: hidden;
    background: var(--page);
    font-family: "Open Sans", Arial, sans-serif;
  }
  .canvas { position: relative; width: 800px; height: 1200px; }

  .card { position: absolute; width: 526px; height: 300px; overflow: hidden; }
  .card--front {
    left: 153px; top: 182px;
    background: var(--card-light);
    border-radius: 10px;
  }
  .card--back {
    left: 140px; top: 733px;
    background: var(--card-dark);
  }

  .skyline-panel {
    position: absolute; left: 347px; top: 128px;
    width: 170px; height: 172px;
    background: linear-gradient(to bottom, rgba(166,191,220,0) 0%, var(--skyline-blue) 45%, var(--skyline-lilac) 100%);
    opacity: 0.75;
    z-index: 0;
  }

  .wordmark {
    position: absolute; z-index: 1;
    display: flex; align-items: center; gap: 8px;
    font-weight: 600; letter-spacing: 0.5px; white-space: nowrap;
  }
  .wordmark__square { width: 14px; height: 14px; }
  .card--front .wordmark { left: 32px; top: 62px; font-size: 24px; color: var(--brand-blue); }
  .card--front .wordmark__square { background: var(--brand-blue); }
  .card--back .wordmark {
    left: 0; right: 0; top: 126px; justify-content: center;
    font-size: 26px; color: var(--white);
  }
  .card--back .wordmark__square { background: var(--white); }

  .motto {
    position: absolute; left: 0; right: 0; top: 170px;
    text-align: center; font-size: 12px; letter-spacing: 0.4px;
    color: var(--accent-orange); font-weight: 600;
  }

  .person { position: absolute; left: 36px; top: 143px; z-index: 1; }
  .person__name { font-size: 22px; font-weight: 400; color: var(--name-blue); line-height: 1.2; }
  .person__title { font-size: 13px; color: var(--text-grey); font-weight: 600; }

  .contacts {
    position: absolute; left: 34px; top: 195px; z-index: 1;
    display: grid; grid-template-columns: 142px auto; row-gap: 8px;
    font-size: 13px; color: var(--text-grey);
  }
  .contact { display: flex; align-items: center; gap: 6px; }
  .contact svg { width: 9px; height: 9px; fill: var(--name-blue); flex: none; }

  .rule {
    position: absolute; left: 34px; top: 248px; z-index: 1;
    width: 386px; height: 1px; background: var(--rule-grey);
  }
  .rule__accent {
    position: absolute; left: 0; top: -1px;
    width: 60px; height: 3px; background: var(--accent-orange);
  }
  .address {
    position: absolute; left: 34px; top: 255px; z-index: 1;
    font-size: 15px; color: var(--text-grey);
  }
</style>
</head>
<body>
<main class="canvas">
  <section class="card card--front" aria-label="Card front">
    <div class="skyline-panel" role="img" aria-label="Faint city skyline decoration in soft blue and silver"></div>

    <div class="wordmark"><span class="wordmark__square"></span>Harlow Building, Inc.</div>

    <div class="person">
      <p class="person__name">Daniel Reyes</p>
      <p class="person__title">Managing Member</p>
    </div>

    <div class="contacts">
      <span class="contact">
        <svg viewBox="0 0 10 10" aria-hidden="true"><path d="M2 0.5 L4 2.5 L3 3.8 Q4 6 6.2 7 L7.5 6 L9.5 8 L8 9.6 Q2 8.5 0.4 2 Z"/></svg>
        (555) 214-3870
      </span>
      <span class="contact">
        <svg viewBox="0 0 10 10" aria-hidden="true"><path d="M0 2 H10 V8.5 H0 Z"/><path d="M0 2 L5 5.5 L10 2" fill="none" stroke="#e6e6e7" stroke-width="0.9"/></svg>
        daniel@example.com
      </span>
      <span class="contact">
        <svg viewBox="0 0 10 10" aria-hidden="true"><path d="M2.5 0 H7.5 V10 H2.5 Z M3.3 1 V8 H6.7 V1 Z"/></svg>
        (555) 308-4192
      </span>
      <span class="contact">
        <svg viewBox="0 0 10 10" aria-hidden="true"><circle cx="5" cy="5" r="5"/><path d="M0 5 H10 M5 0 V10 M5 0 Q2 5 5 10 M5 0 Q8 5 5 10" fill="none" stroke="#e6e6e7" stroke-width="0.7"/></svg>
        www.example.com
      </span>
    </div>

    <div class="rule"><span class="rule__accent"></span></div>
    <p class="address">2250 Ridgeview Drive, Fairbank, CA 95120</p>
  </section>

  <section class="card card--back" aria-label="Card back">
    <div class="wordmark"><span class="wordmark__square"></span>Harlow Building, Inc.</div>
    <p class="motto">Built on integrity... Inspired by commitment.</p>
  </section>
</main>
</body>
</html>
```